Every Shelf Set Neatly or ESN Organized needs a business card design. ESN Organized is a professi

We need a business card design that is clean, sharp and conveys a sense of organization. I already have a logo.

Target Market(s)

Families (specifically mothers), small business owners, parents, seniors

Industry/Entity Type

Business

Contact Information for Business Card

My website is www.esnorganized-example.com and my Facebook page is http://www.sociallink-example.com/everyshelfsetneatly. The phone number is 418-552-7094 and I want to be listed as Lorna M. Pelham, Owner

Requirements
Must have
• My logo.

```html
<!DOCTYPE html>
<html lang="en">
<head>
<meta charset="utf-8">
<title>ESN Organized – Business Card</title>
<link rel="stylesheet" href="https://fonts.googleapis.com/css2?family=Open+Sans:ital,wght@0,400;0,600;0,700;1,400&display=swap">
<style>
  :root {
    --canvas-bg: #8c8c8c;
    --card-light: #e9e9eb;
    --card-dark: #000000;
    --brand-blue: #1470c8;
    --ink: #3a3a3a;
    --ink-soft: #555555;
    --white: #ffffff;
  }
  * { box-sizing: border-box; margin: 0; padding: 0; }
  html, body {
    width: 1105px;
    height: 1200px;
    overflow: hidden;
  }
  body {
    background: var(--canvas-bg);
    font-family: "Open Sans", Arial, sans-serif;
    position: relative;
  }
  .card {
    position: absolute;
    left: 180px;
    width: 745px;
    height: 427px;
  }
  .card--front { top: 120px; background: var(--card-light); }
  .card--back  { top: 650px; background: var(--card-dark); }

  .brand-name {
    position: absolute;
    left: 55px;
    top: 82px;
    display: flex;
    align-items: center;
    gap: 12px;
    color: var(--brand-blue);
    font-weight: 600;
    font-size: 30px;
    letter-spacing: 0.5px;
  }
  .brand-dot {
    width: 14px;
    height: 14px;
    border-radius: 50%;
    background: var(--brand-blue);
  }

  .contact-list {
    position: absolute;
    left: 55px;
    top: 280px;
    list-style: none;
  }
  .contact-item {
    display: flex;
    align-items: center;
    gap: 9px;
    height: 29px;
    color: var(--ink-soft);
    font-size: 19px;
  }
  .contact-icon { width: 18px; height: 18px; flex: none; }

  .name-tab {
    position: absolute;
    left: 414px;
    top: 277px;
    width: 331px;
    height: 93px;
    background: var(--brand-blue);
    border-radius: 46px 0 0 46px;
    color: var(--white);
    text-align: right;
    padding: 14px 47px 0 0;
  }
  .name-tab__name {
    font-weight: 700;
    font-size: 25px;
    line-height: 34px;
    letter-spacing: 0.3px;
  }
  .name-tab__title {
    font-weight: 400;
    font-size: 19px;
    line-height: 26px;
  }

  .back-brand {
    position: absolute;
    left: 0;
    right: 0;
    top: 140px;
    text-align: center;
    color: var(--brand-blue);
    font-weight: 400;
    font-size: 64px;
    letter-spacing: 2px;
  }
  .back-web {
    position: absolute;
    left: 0;
    right: 0;
    top: 350px;
    text-align: center;
    color: var(--white);
    font-style: italic;
    font-size: 20px;
    letter-spacing: 5px;
  }
</style>
</head>
<body>
  <section class="card card--front" aria-label="Business card front">
    <div class="brand-name"><span class="brand-dot"></span>Every Shelf Set Neatly</div>

    <ul class="contact-list">
      <li class="contact-item">
        <svg class="contact-icon" viewBox="0 0 24 24" aria-hidden="true">
          <path fill="#1470c8" d="M6.6 10.8a15.1 15.1 0 0 0 6.6 6.6l2.2-2.2c.3-.3.7-.4 1-.2 1.1.4 2.3.6 3.6.6.6 0 1 .4 1 1V20c0 .6-.4 1-1 1A17 17 0 0 1 3 4c0-.6.4-1 1-1h3.5c.6 0 1 .4 1 1 0 1.3.2 2.5.6 3.6.1.3 0 .7-.2 1z"/>
        </svg>
        418-552-7094
      </li>
      <li class="contact-item">
        <svg class="contact-icon" viewBox="0 0 24 24" aria-hidden="true">
          <circle cx="12" cy="12" r="10" fill="#1470c8"/>
          <path d="M2 12h20M12 2c3 3 3 17 0 20M12 2c-3 3-3 17 0 20" stroke="#e9e9eb" stroke-width="1.4" fill="none"/>
        </svg>
        www.esnorganized-example.com
      </li>
      <li class="contact-item">
        <svg class="contact-icon" viewBox="0 0 24 24" aria-hidden="true">
          <rect x="2" y="2" width="20" height="20" rx="2" fill="#1470c8"/>
        </svg>
        everyshelfsetneatly
      </li>
    </ul>

    <div class="name-tab">
      <p class="name-tab__name">LORNA M. PELHAM</p>
      <p class="name-tab__title">OWNER</p>
    </div>
  </section>

  <section class="card card--back" aria-label="Business card back">
    <p class="back-brand">ESN Organized</p>
    <p class="back-web">www.esnorganized-example.com</p>
  </section>
</body>
</html>
```